Website for Boutique Property Consultancy in UK

We are looking to designing a website for our Property Consultancy Services that follows a minimalistic clean style that is also bold and intriguing.
The website will be based on one landing page and a link to Profile Page and email link.

Dominant features will be the company logo or icon and colours.

Brand colours provided for guidance.

Looking to achieve a minimalistic clean style that is also bold and intriguing.

"Updated"
Page 1 - Landing Page with the Hyperlinks to Pick a Service, Training Portal and Quill Meadow Portal. example landing page https://brantwistle.co.uk/

Page 2 - Shows all the Services and Sectors

Target Market(s)

Occupier Clients, Tech Companies, Property Developers, Infrastructure Clients and Major Consultants

Industry/Entity Type

Construction

Coding

Coded - Design and coding required

Number of Pages Required

2 page

Font styles to use
Other font styles liked:
• Century Gothic or Futuris (Headings)

Colors
0054AA
0677BA
7BADD7
CADEEF
E8F1F8
00AB8E
00BBA5
67D7C9
C6EFE9
E9F9F6

Requirements
Must have
• Company Logo, link to enquiry and Profile

```html
<!DOCTYPE html>
<html lang="en">
<head>
<meta charset="utf-8">
<title>Tarrow Field – Landing Page</title>
<link rel="stylesheet" href="https://fonts.googleapis.com/css2?family=Questrial&display=swap">
<style>
  :root {
    --green: #1ec075;
    --navy: #131338;
    --mist: #e9e9eb;
    --page-bg: #ffffff;
    --rule: #d0d0d5;
    --soft-text: #ffffff;
    --label: #555560;
  }
  * { margin: 0; padding: 0; box-sizing: border-box; }
  html, body { width: 888px; height: 1200px; overflow: hidden; background: var(--page-bg); }
  body { position: relative; font-family: "Questrial", "Century Gothic", sans-serif; color: var(--navy); }

  /* Brand sheet */
  .brand-sheet { position: absolute; left: 0; top: 0; width: 888px; height: 200px; }
  .brand-sheet__logo { position: absolute; left: 172px; top: 96px; font-size: 20px; letter-spacing: 0.5px; color: var(--navy); }
  .brand-sheet__divider { position: absolute; top: 80px; width: 1px; height: 70px; background: var(--rule); }
  .brand-sheet__divider--one { left: 359px; }
  .brand-sheet__divider--two { left: 583px; top: 78px; }
  .brand-sheet__title { position: absolute; font-size: 20px; font-weight: 400; color: var(--navy); }
  .brand-sheet__title--fonts { left: 430px; top: 76px; }
  .brand-sheet__title--colors { left: 654px; top: 74px; }
  .brand-sheet__font-name { position: absolute; left: 430px; top: 111px; font-size: 13px; color: var(--navy); }
  .swatch { position: absolute; top: 103px; width: 31px; height: 31px; border-radius: 50%; }
  .swatch--green { left: 655px; background: var(--green); }
  .swatch--navy { left: 694px; background: var(--navy); }
  .swatch--mist { left: 734px; background: var(--mist); box-shadow: 0 1px 3px rgba(0,0,0,0.12); }
  .swatch__label { position: absolute; top: 139px; font-size: 7px; letter-spacing: 0.3px; color: var(--label); }

  /* Landing page */
  .landing { position: absolute; left: 44px; top: 300px; width: 800px; height: 500px; background: linear-gradient(180deg, #ececef 0%, #e3e3e7 100%); overflow: hidden; box-shadow: 0 6px 24px rgba(0,0,0,0.08); }
  .site-header { position: absolute; left: 0; top: 0; width: 100%; height: 43px; border-bottom: 1px solid #dcdce0; }
  .site-header__logo { position: absolute; left: 50px; top: 14px; font-size: 12.5px; color: var(--navy); letter-spacing: 0.3px; }
  .site-nav { position: absolute; top: 17px; font-size: 7px; color: var(--navy); white-space: nowrap; }
  .site-nav--service { left: 512px; }
  .site-nav--service::after { content: ""; position: absolute; left: 7px; right: 0; bottom: -4px; height: 1px; background: var(--green); }
  .site-nav--training { left: 588px; }
  .site-nav--portal { left: 664px; }
  .site-header__social { position: absolute; left: 727px; top: 10px; width: 23px; height: 23px; border-radius: 50%; background: var(--green); }

  .hero-image { position: absolute; left: 375px; top: 150px; width: 425px; height: 350px; background: linear-gradient(180deg, #8a8a92 0%, #45454d 35%, #25252c 70%, #1b1b21 100%); }
  .hero-panel { position: absolute; left: 0; top: 256px; width: 375px; height: 244px; background: linear-gradient(180deg, #dcdce0 0%, #cfcfd4 100%); }
  .hero-panel__eyebrow { position: absolute; left: 51px; top: 50px; font-size: 6.5px; letter-spacing: 2.6px; text-transform: uppercase; color: var(--navy); white-space: nowrap; }
  .hero-panel__eyebrow em { font-style: normal; color: var(--green); }
  .hero-panel__headline { position: absolute; left: 50px; top: 63px; font-size: 24px; line-height: 29px; font-weight: 400; color: var(--soft-text); white-space: nowrap; }
  .hero-panel__headline strong { font-weight: 400; color: var(--navy); }
  .hero-panel__meta { position: absolute; left: 51px; top: 141px; font-size: 7px; color: var(--soft-text); white-space: nowrap; }
  .hero-panel__badge { position: absolute; left: 51px; top: 172px; width: 50px; height: 15px; border-radius: 3px; background: #f4f4f6; opacity: 0.85; }
  .hero-panel__cta { position: absolute; left: 279px; top: 150px; width: 44px; height: 44px; }
</style>
</head>
<body>
  <section class="brand-sheet" aria-label="Brand guide">
    <div class="brand-sheet__logo">tarrow field</div>
    <div class="brand-sheet__divider brand-sheet__divider--one"></div>
    <h2 class="brand-sheet__title brand-sheet__title--fonts">Fonts</h2>
    <p class="brand-sheet__font-name">Century Gothic</p>
    <div class="brand-sheet__divider brand-sheet__divider--two"></div>
    <h2 class="brand-sheet__title brand-sheet__title--colors">Colors:</h2>
    <span class="swatch swatch--green"></span>
    <span class="swatch swatch--navy"></span>
    <span class="swatch swatch--mist"></span>
    <span class="swatch__label" style="left:655px">#1ec075</span>
    <span class="swatch__label" style="left:695px">#131338</span>
    <span class="swatch__label" style="left:733px">#e9e9eb</span>
  </section>

  <main class="landing">
    <header class="site-header">
      <div class="site-header__logo">tarrow field</div>
      <span class="site-nav site-nav--service">+ Pick a Service</span>
      <span class="site-nav site-nav--training">+ Training Portal</span>
      <span class="site-nav site-nav--portal">+ Quill Meadow</span>
      <span class="site-header__social" aria-label="Professional profile link"></span>
    </header>

    <div class="hero-image" role="img" aria-label="Black and white photo of tall city office towers"></div>

    <section class="hero-panel">
      <p class="hero-panel__eyebrow">Welcome to <em>Tarrow Field</em></p>
      <h1 class="hero-panel__headline">Delivering <strong>Value</strong> and<br>Redefining <strong>Boundaries</strong></h1>
      <p class="hero-panel__meta">By Referral Only &nbsp;|&nbsp; Email/Profile</p>
      <div class="hero-panel__badge" aria-label="Accreditation badge"></div>
      <svg class="hero-panel__cta" viewBox="0 0 44 44" aria-label="Continue">
        <circle cx="22" cy="22" r="21" fill="none" stroke="#1ec075" stroke-width="1"/>
        <path d="M15 22h14M24 17l5 5-5 5" fill="none" stroke="#1ec075" stroke-width="1.2" stroke-linecap="round" stroke-linejoin="round"/>
      </svg>
    </section>
  </main>
</body>
</html>
```